Harbourline Electrical Solutions

On one side. LOGO (underneath:) Commercial Industrial Residential

- NAME & CONTACT DETAILS

Marcus T. Hollings
Project Manager

(Cell icon) (441) 555-0187
(Email icon) hlelectricalsolutions@mailvento.com
(Facebook & Instagram icons )@hlelectricalsolutions

Other side: LOGO - underneath ELECTRICAL CONSTRUCTION & MAINTENANCE . LED LIGHTING & AUTOMATION . LIFE SAFETY SYSTEMS (FIRE ALARM / SECURITY) . DATA & COMMUNICATION

```html
<!DOCTYPE html>
<html lang="en">
<head>
<meta charset="UTF-8">
<title>Harbourline Electrical Solutions – Business Card</title>
<link href="https://fonts.googleapis.com/css2?family=Montserrat:wght@600&family=Poppins:wght@400;500;700&display=swap" rel="stylesheet">
<style>
  :root {
    --teal: #11566b;
    --charcoal: #4a4a4c;
    --ink: #3c3c3e;
    --paper: #ffffff;
    --backdrop: #e6e8ea;
  }
  * { margin: 0; padding: 0; box-sizing: border-box; }
  html, body { width: 1200px; height: 880px; overflow: hidden; }
  body {
    background: var(--backdrop);
    font-family: "Poppins", sans-serif;
    display: flex;
    flex-direction: column;
    align-items: center;
    justify-content: center;
    gap: 40px;
  }
  .card {
    position: relative;
    width: 640px;
    height: 366px;
    overflow: hidden;
    box-shadow: 0 6px 18px rgba(0,0,0,0.18);
  }

  /* Back side */
  .card-back { background: var(--teal); color: var(--paper); }
  .wordmark {
    display: flex;
    align-items: center;
    gap: 16px;
    font-family: "Montserrat", sans-serif;
    font-weight: 600;
    text-transform: uppercase;
    letter-spacing: 2px;
    line-height: 1.12;
  }
  .wordmark-square { width: 22px; height: 22px; flex: none; }
  .card-back .wordmark {
    position: absolute; left: 150px; top: 92px;
    font-size: 26px; color: var(--paper);
  }
  .card-back .wordmark-square { background: var(--paper); }
  .services {
    position: absolute; left: 60px; right: 40px; bottom: 70px;
    font-size: 13.5px; font-weight: 500; line-height: 1.55;
  }

  /* Front side */
  .card-front { background: var(--paper); }
  .card-front .wordmark {
    position: absolute; left: 50px; top: 44px;
    font-size: 24px; color: var(--teal);
  }
  .card-front .wordmark-square { background: var(--teal); }
  .rule-top {
    position: absolute; left: 380px; right: 44px; top: 92px;
    height: 1px; background: var(--teal);
  }
  .person { position: absolute; left: 50px; top: 176px; }
  .person-name {
    font-weight: 700; font-size: 20px; color: var(--teal);
    text-transform: uppercase; letter-spacing: 0.5px;
  }
  .person-role { font-size: 15px; color: var(--ink); margin-top: 2px; }
  .rule-person {
    width: 430px; height: 1px; background: var(--teal); margin: 10px 0 12px;
  }
  .contacts { list-style: none; font-size: 14.5px; color: var(--ink); }
  .contacts li { display: flex; align-items: center; gap: 8px; height: 24px; }
  .icon {
    width: 18px; height: 18px; border-radius: 50%;
    background: var(--teal); flex: none;
    display: flex; align-items: center; justify-content: center;
  }
  .icon svg { width: 10px; height: 10px; }
  .band-grey {
    position: absolute; left: 0; bottom: 0;
    width: 67%; height: 16px; background: var(--charcoal);
  }
  .band-grey-step {
    position: absolute; left: 57%; bottom: 0;
    width: 10%; height: 44px; background: var(--charcoal);
  }
  .band-teal {
    position: absolute; right: 0; bottom: 0;
    width: 31.5%; height: 62px; background: var(--teal);
  }
</style>
</head>
<body>

  <section class="card card-back" aria-label="Card back">
    <div class="wordmark">
      <span class="wordmark-square"></span>
      <span>Harbourline<br>Electrical<br>Solutions</span>
    </div>
    <p class="services">
      Electrical Construction &amp; Maintenance | LED Lighting &amp; Automation<br>
      Life Safety Systems (FIRE ALARM / SECURITY) | Data &amp; Communication
    </p>
  </section>

  <section class="card card-front" aria-label="Card front">
    <div class="wordmark">
      <span class="wordmark-square"></span>
      <span>Harbourline<br>Electrical<br>Solutions</span>
    </div>
    <div class="rule-top"></div>

    <div class="person">
      <p class="person-name">Marcus T. Hollings</p>
      <p class="person-role">Project Manager</p>
      <div class="rule-person"></div>
      <ul class="contacts">
        <li>
          <span class="icon">
            <svg viewBox="0 0 10 10"><rect x="2.5" y="0.5" width="5" height="9" rx="1" fill="none" stroke="#fff" stroke-width="1.2"/></svg>
          </span>
          (441) 555-0187
        </li>
        <li>
          <span class="icon">
            <svg viewBox="0 0 10 10"><rect x="0.8" y="2" width="8.4" height="6" fill="none" stroke="#fff" stroke-width="1.1"/><path d="M0.8 2 L5 5.5 L9.2 2" fill="none" stroke="#fff" stroke-width="1.1"/></svg>
          </span>
          hlelectricalsolutions@mailvento.com
        </li>
        <li>
          <span class="icon"></span>
          <span class="icon"></span>
          @hlelectricalsolutions
        </li>
      </ul>
    </div>

    <div class="band-grey"></div>
    <div class="band-grey-step"></div>
    <div class="band-teal"></div>
  </section>

</body>
</html>
```